Franchise Power Point

Looking to add a strong design element to a very basic power point presentation about how to find the ideal franchise match. My website is www.tallowbrookventuring.com and www.unitquest/KWendell

```html
<!DOCTYPE html>
<html lang="en">
<head>
<meta charset="utf-8">
<title>Smart Franchise Decisions Using Logic and Intuition</title>
<link href="https://fonts.googleapis.com/css2?family=Young+Serif&family=Arimo:wght@400;700&family=Montserrat:wght@400;500&display=swap" rel="stylesheet">
<style>
:root{
  --navy:#1b3050;
  --gold:#fbbd1a;
  --backdrop:#767676;
  --white:#ffffff;
  --mist:#f1f1f1;
  --ink:#1b2b44;
  --grey-text:#5b5f66;
}
*{margin:0;padding:0;box-sizing:border-box}
html,body{width:1200px;height:4005px;overflow:hidden;background:var(--backdrop)}
body{position:relative;font-family:"Arimo",Arial,sans-serif}
.slide{position:absolute;width:1105px;height:621px;overflow:hidden;background:var(--white)}
.serif{font-family:"Young Serif",Georgia,serif;font-weight:400}
.abs{position:absolute}
.brand{position:absolute;display:flex;flex-direction:column;align-items:flex-start}
.brand-name{font-family:"Arimo",Arial,sans-serif;font-weight:700;color:var(--navy);line-height:1;letter-spacing:.2px}
.brand-tag{font-family:"Arimo",Arial,sans-serif;font-weight:400;color:var(--navy);white-space:nowrap}
.brand.on-dark .brand-name,.brand.on-dark .brand-tag{color:var(--white)}
.checklist{list-style:none;position:absolute;inset:0}
.checklist li{position:absolute;display:flex;align-items:flex-start;gap:10px;font-weight:700;font-size:17px;line-height:26px;text-transform:uppercase;letter-spacing:.1px;white-space:nowrap}
.checklist svg{flex:none;margin-top:6px;width:14px;height:14px}
.photo{position:absolute}
.contact-text{font-family:"Montserrat",sans-serif;font-size:15px;line-height:23px;color:var(--ink)}
.dozen-list li{position:absolute;white-space:nowrap;display:flex;align-items:center;gap:12px}
.dozen-list li::before{content:"";width:8px;height:8px;border-radius:50%;background:var(--gold)}
</style>
</head>
<body>
<svg width="0" height="0" style="position:absolute">
  <defs>
    <symbol id="tick" viewBox="0 0 14 14">
      <circle cx="7" cy="7" r="7" fill="#fbbd1a"/>
      <path d="M3.8 7.2 6 9.3 10.2 4.9" fill="none" stroke="#ffffff" stroke-width="1.8" stroke-linecap="round" stroke-linejoin="round"/>
    </symbol>
  </defs>
</svg>

<!-- Title slide -->
<section class="slide title-slide" style="left:50px;top:57px;width:1103px;background:var(--navy)">
  <div class="photo" role="img" aria-label="Portrait photo of the presenter" style="left:-6px;top:103px;width:512px;height:512px;border-radius:50%;background:radial-gradient(circle at 45% 40%,#e9d6b8 0%,#d8c6ad 35%,#b8473f 80%,#9a2f2c 100%)"></div>
  <svg class="abs" style="left:0;top:0" width="600" height="621" viewBox="0 0 600 621">
    <path d="M 0 150 A 300 300 0 0 1 550 360" fill="none" stroke="#fbbd1a" stroke-width="19"/>
  </svg>
  <h1 class="serif abs" style="left:573px;top:186px;color:var(--gold);font-size:51px;line-height:71px;white-space:nowrap">Smart Franchise<br>Decisions Using<br>Logic and Intuition</h1>
</section>

<!-- Key questions slide -->
<section class="slide questions-slide" style="left:45px;top:712px">
  <div class="abs" style="left:0;top:0;width:1105px;height:309px;background:var(--navy)"></div>
  <h2 class="serif abs" style="left:81px;top:50px;color:var(--white);font-size:34px;line-height:43px">Sample Key Questions for the Educated<br>Approach</h2>
  <div class="brand on-dark" style="left:918px;top:52px">
    <span class="brand-name" style="font-size:22px">UnitQuest</span>
    <span class="brand-tag" style="font-size:8px;margin-top:4px">Franchise Ownership Advisory</span>
  </div>
  <div class="abs question-card" style="left:81px;top:179px;width:957px;height:365px;background:var(--white);box-shadow:0 8px 24px rgba(0,0,0,.14)">
    <ul class="checklist" style="color:var(--ink)">
      <li style="left:37px;top:40px"><svg viewBox="0 0 14 14"><use href="#tick"/></svg>Proper investment level</li>
      <li style="left:37px;top:80px"><svg viewBox="0 0 14 14"><use href="#tick"/></svg>Skill set and background / personality matching</li>
      <li style="left:37px;top:127px"><svg viewBox="0 0 14 14"><use href="#tick"/></svg>Return goals – short, mid and long term</li>
      <li style="left:37px;top:167px"><svg viewBox="0 0 14 14"><use href="#tick"/></svg>Employee profile: numbers &amp; backgrounds</li>
      <li style="left:37px;top:212px"><svg viewBox="0 0 14 14"><use href="#tick"/></svg>Sales, marketing and advertising</li>
      <li style="left:37px;top:253px"><svg viewBox="0 0 14 14"><use href="#tick"/></svg>Concerns around the economy</li>
      <li style="left:37px;top:292px"><svg viewBox="0 0 14 14"><use href="#tick"/></svg>Need vs want</li>
      <li style="left:593px;top:40px"><svg viewBox="0 0 14 14"><use href="#tick"/></svg>Residual / repeat / reoccurring</li>
      <li style="left:593px;top:80px"><svg viewBox="0 0 14 14"><use href="#tick"/></svg>Status</li>
      <li style="left:593px;top:127px"><svg viewBox="0 0 14 14"><use href="#tick"/></svg>B2B vs B2C</li>
      <li style="left:593px;top:167px"><svg viewBox="0 0 14 14"><use href="#tick"/></svg>Full time vs part time vs.<br>managed services</li>
    </ul>
  </div>
</section>

<!-- Research method slide -->
<section class="slide research-slide" style="left:45px;top:1365px">
  <h2 class="serif abs" style="left:37px;top:32px;color:var(--ink);font-size:36px">The Research Method</h2>
  <div class="brand" style="left:960px;top:36px">
    <span class="brand-name" style="font-size:19px">UnitQuest</span>
    <span class="brand-tag" style="font-size:7px;margin-top:3px">Franchise Ownership Advisory</span>
  </div>
  <div class="abs method-panel" style="left:25px;top:101px;width:862px;height:446px;background:var(--navy);border-radius:4px">
    <ul class="checklist" style="color:var(--white)">
      <li style="left:37px;top:23px"><svg viewBox="0 0 14 14"><use href="#tick"/></svg>Define your ideal match</li>
      <li style="left:37px;top:63px"><svg viewBox="0 0 14 14"><use href="#tick"/></svg>Establish contact with target franchisor</li>
      <li style="left:37px;top:110px"><svg viewBox="0 0 14 14"><use href="#tick"/></svg>Work through their standard process</li>
      <li style="left:37px;top:150px"><svg viewBox="0 0 14 14"><use href="#tick"/></svg>Review FDD</li>
      <li style="left:37px;top:195px"><svg viewBox="0 0 14 14"><use href="#tick"/></svg>Validate with franchisees</li>
      <li style="left:37px;top:236px"><svg viewBox="0 0 14 14"><use href="#tick"/></svg>Explore financing options</li>
      <li style="left:37px;top:274px"><svg viewBox="0 0 14 14"><use href="#tick"/></svg>Discuss territory</li>
      <li style="left:37px;top:313px"><svg viewBox="0 0 14 14"><use href="#tick"/></svg>Put together cash flow projections</li>
      <li style="left:37px;top:351px"><svg viewBox="0 0 14 14"><use href="#tick"/></svg>Attend discovery day</li>
      <li style="left:37px;top:391px"><svg viewBox="0 0 14 14"><use href="#tick"/></svg>Make a decision</li>
    </ul>
  </div>
  <svg class="abs" style="left:600px;top:60px" width="500" height="300" viewBox="0 0 500 300">
    <path d="M 6 240 A 250 250 0 0 1 490 210" fill="none" stroke="#fbbd1a" stroke-width="19"/>
  </svg>
  <div class="photo" role="img" aria-label="Photo of two people meeting at a desk with laptops" style="left:627px;top:100px;width:450px;height:450px;border-radius:50%;background:linear-gradient(135deg,#d9d4cc 0%,#b7a58f 45%,#6f7f96 80%,#3c4a5e 100%)"></div>
</section>

<!-- Dam or river slide -->
<section class="slide river-slide" style="left:45px;top:2018px">
  <div class="brand" style="left:960px;top:36px">
    <span class="brand-name" style="font-size:19px">UnitQuest</span>
    <span class="brand-tag" style="font-size:7px;margin-top:3px">Franchise Ownership Advisory</span>
  </div>
  <div class="photo" role="img" aria-label="Photo of a river winding through a rocky canyon" style="left:68px;top:67px;width:524px;height:554px;background:linear-gradient(180deg,#c9cfc7 0%,#8a8f7d 25%,#5f6b52 50%,#2f6b6b 75%,#2b5a5d 100%)"></div>
  <svg class="abs" style="left:0;top:0" width="620" height="621" viewBox="0 0 620 621">
    <path d="M 0 290 A 300 300 0 0 1 592 385" fill="none" stroke="#fbbd1a" stroke-width="19"/>
  </svg>
  <p class="serif abs" style="left:684px;top:262px;color:var(--ink);font-size:35px;line-height:47px;white-space:nowrap">Are you the dam or<br>are you the River?</p>
</section>

<!-- Top dozen slide -->
<section class="slide dozen-slide" style="left:45px;top:2672px">
  <div class="brand" style="left:960px;top:36px">
    <span class="brand-name" style="font-size:19px">UnitQuest</span>
    <span class="brand-tag" style="font-size:7px;margin-top:3px">Franchise Ownership Advisory</span>
  </div>
  <div class="abs" style="left:177px;top:509px;width:866px;height:8px;background:var(--gold)"></div>
  <div class="abs" style="left:1035px;top:188px;width:8px;height:329px;background:var(--gold)"></div>
  <div class="abs" style="left:53px;top:135px;width:974px;height:372px;background:var(--mist)"></div>
  <h2 class="serif abs" style="left:96px;top:182px;color:var(--ink);font-size:35px;white-space:nowrap">My Top Dozen for 2024</h2>
  <ul class="abs dozen-list" style="left:96px;top:0;list-style:none;font-family:'Montserrat',sans-serif;font-size:14px;color:var(--grey-text)">
    <li style="top:247px">Emergency Restoration</li>
    <li style="top:288px">Low Status Options</li>
    <li style="top:328px">Home Services</li>
    <li style="top:369px">Rental Options</li>
    <li style="top:409px">Clothing Recycling</li>
    <li style="top:449px">Food Trucks / Restaurants</li>
  </ul>
  <div class="photo" role="img" aria-label="Photo of a smiling man reading a tablet at a table with coffee cups" style="left:569px;top:89px;width:371px;height:469px;background:linear-gradient(160deg,#e6e3dc 0%,#cfc8bb 40%,#a59483 70%,#e9e7e2 100%)"></div>
</section>

<!-- Closing slide -->
<section class="slide closing-slide" style="left:50px;top:3325px;width:1105px;height:622px">
  <div class="photo" role="img" aria-label="Navy-tinted photo of a smiling woman in an office" style="left:0;top:0;width:474px;height:622px;background:linear-gradient(150deg,#253d5f 0%,#1b3050 55%,#15273f 100%)"></div>
  <svg class="abs" style="left:0;top:0" width="474" height="622" viewBox="0 0 474 622">
    <path d="M 160 430 A 380 380 0 0 1 370 622" fill="none" stroke="#fbbd1a" stroke-width="22"/>
  </svg>
  <div class="brand" style="left:553px;top:118px">
    <span class="brand-name" style="font-size:52px">UnitQuest</span>
    <span class="brand-tag" style="font-size:19px;margin-top:10px">Franchise Ownership Advisory</span>
  </div>
  <h2 class="serif abs" style="left:553px;top:234px;color:var(--ink);font-size:38px">THANK YOU</h2>
  <p class="serif abs" style="left:558px;top:311px;color:var(--ink);font-size:21px">COURTESY OF:</p>

  <svg class="abs" style="left:558px;top:376px" width="44" height="44" viewBox="0 0 44 44">
    <circle cx="22" cy="22" r="22" fill="#fbbd1a"/>
    <path d="M22 12a7 7 0 0 0-7 7c0 5 7 13 7 13s7-8 7-13a7 7 0 0 0-7-7zm0 9.5a2.5 2.5 0 1 1 0-5 2.5 2.5 0 0 1 0 5z" fill="#fff"/>
  </svg>
  <p class="abs contact-text" style="left:617px;top:377px">4120 Harbor Birch Road,<br>#210 Lakemont, MN 55901</p>

  <svg class="abs" style="left:856px;top:376px" width="44" height="44" viewBox="0 0 44 44">
    <circle cx="22" cy="22" r="22" fill="#fbbd1a"/>
    <path d="M16.5 12.5l3 .5 1.5 4.5-2 1.5a11 11 0 0 0 5.5 5.5l1.5-2 4.5 1.5.5 3c-1 1.5-2.5 2.5-4.5 2.5C20 29.5 14.5 24 14.5 17c0-2 1-3.5 2-4.5z" fill="#fff"/>
  </svg>
  <p class="serif abs" style="left:915px;top:374px;font-size:15px;color:var(--ink)">PHONE</p>
  <p class="abs contact-text" style="left:917px;top:398px">555.014.2376</p>

  <svg class="abs" style="left:558px;top:462px" width="44" height="44" viewBox="0 0 44 44">
    <circle cx="22" cy="22" r="22" fill="#fbbd1a"/>
    <rect x="13" y="15" width="18" height="13" rx="2" fill="#fff"/>
    <path d="M13.5 16l8.5 6.5 8.5-6.5" fill="none" stroke="#fbbd1a" stroke-width="1.6"/>
  </svg>
  <p class="serif abs" style="left:620px;top:461px;font-size:15px;color:var(--ink)">EMAIL</p>
  <p class="abs contact-text" style="left:622px;top:486px">kwendell@unitquest.com</p>
</section>
</body>
</html>
```